Cyber Security Site Design (Products & Consulting)

I need my website redesigned to be engaging, clean, efficient and modern. My company (when its up and running) is going to be concentrated on two things: a few specific products for cyber security as well as cyber security consulting services. The background I bring to the field is having worked with small companies all the way to the largest government organizations and advising them on their security posture and how to improve it. We need the ability to add products and services easily.

For a sample product, you can use either Tarnet (http://www.tarnet-relay.org/) or Verodyne Ashmantle (https://www.verodyne.com/products/relay-hx-and-fortified-edge-portal).

It will replace https://lumerafieldworks.com/

Target Market(s)

Cyber Security professionals in all verticals

Coding

Coded - Design and coding required

Number of Pages Required

4 page

Font styles to use
Sans Serif

Colors
6b449b

Requirements
Must have
• Ability to easily modify
• Have main page
• Have product specific pages
• Have consulting services pages
• Have executive team information
• Clean, modern design
• Usage of the logo and its color scheme
Nice to have
• I like the idea of a left collapsed sidebar (so icons only) that can expand for text.
• I am also open to a very unique landing page, possibly a shape in the middle (hexagons maybe?) with each of the options there.
Should not have
• Nothing that looks like it came out of a hacker movie

```html
<!DOCTYPE html>
<html lang="en">
<head>
<meta charset="utf-8">
<title>Lumera Fieldworks – Site Design</title>
<link href="https://fonts.googleapis.com/css2?family=Quicksand:wght@400;500;600&family=Open+Sans:wght@400;600&display=swap" rel="stylesheet">
<style>
:root{
  --board:#cfcfcf;
  --purple:#6b449b;
  --purple-deep:#4f2a8a;
  --purple-night:#2a0d5e;
  --lavender:#ece3f6;
  --ink:#3a3a3a;
  --muted:#777;
  --white:#fff;
  --footer:#2b2b2b;
}
*{box-sizing:border-box;margin:0;padding:0}
html,body{width:1030px;height:1200px;overflow:hidden}
body{background:var(--board);font-family:"Quicksand",sans-serif;color:var(--ink);position:relative}

/* ---------- Landing screen ---------- */
.landing{position:absolute;left:10px;top:16px;width:498px;height:256px;background:var(--white)}
.landing-hero{position:absolute;left:0;top:0;width:498px;height:232px;
  background:radial-gradient(ellipse at 50% 45%,#7a3fc4 0%,#4a1a92 45%,#2a0a62 100%)}
.landing-brand{position:absolute;left:0;right:0;top:8px;display:flex;justify-content:center;align-items:center;gap:5px;
  color:var(--white);font-weight:600;font-size:12px;letter-spacing:.3px}
.brand-square{width:9px;height:9px;border:2px solid currentColor}
.hex-option{position:absolute;width:108px;height:94px}
.hex-option svg{position:absolute;inset:0}
.hex-label{position:absolute;left:0;right:0;top:52px;text-align:center;color:var(--purple);font-size:10px;font-weight:500;line-height:12px}
.landing-footer{position:absolute;left:0;bottom:0;width:498px;height:24px;display:flex;align-items:center;justify-content:space-between;padding:0 76px 0 60px;
  font-family:"Open Sans",sans-serif;font-size:5px;color:#444}
.social{display:flex;gap:6px}
.social span{width:6px;height:6px;border-radius:50%;background:#333;display:block}

/* ---------- Home page ---------- */
.page{position:absolute;left:522px;top:17px;width:498px;height:1158px;background:var(--white)}
.site-header{height:36px;display:flex;align-items:center;justify-content:space-between;padding:0 60px}
.brand{display:flex;align-items:center;gap:5px;color:var(--purple-deep);font-weight:600;font-size:10px}
.brand .brand-square{width:8px;height:8px}
.nav{display:flex;gap:15px;font-size:6px;color:#555}
.nav .active{color:var(--purple)}
.hero{position:relative;height:219px;background:linear-gradient(100deg,#3a1a6e 0%,#5a33a0 45%,#7a52c8 75%,#5c3aa6 100%)}
.hero-title{position:absolute;left:60px;top:90px;color:var(--white);font-size:16px;font-weight:400;line-height:18px}
.btn-light{position:absolute;left:60px;top:130px;background:var(--white);color:var(--purple);font-size:6.5px;padding:4px 6px;border-radius:1px}
.hero-arrow{position:absolute;top:103px;width:10px;height:12px}
section{position:relative}
.sec-title{color:var(--purple-deep);font-size:14px;font-weight:500}
.body-text{font-size:8px;line-height:12.6px;color:var(--ink)}
.btn{display:inline-block;background:var(--purple-deep);color:var(--white);font-size:6.5px;padding:4px 6px;border-radius:1px}
.about{height:158px}
.about .sec-title{position:absolute;left:60px;top:30px}
.about .body-text{position:absolute;left:60px;top:52px;width:264px}
.about .btn{position:absolute;left:60px;top:109px}
.ring{position:absolute;width:92px;height:92px;border:7px solid var(--purple-deep);border-radius:50%}
.products{height:214px;background:var(--lavender)}
.center-title{position:absolute;left:0;right:0;text-align:center}
.products .center-title{top:30px}
.product-card{position:absolute;top:57px;width:180px;height:125px}
.product-img{width:180px;height:113px}
.product-caption{position:absolute;left:6px;right:6px;top:101px;height:23px;background:var(--white);text-align:center;line-height:23px;color:var(--purple-deep);font-size:8.5px;font-weight:500}
.slide-arrow{position:absolute;top:108px;width:8px;height:12px}
.consulting{height:159px}
.consulting .sec-title{position:absolute;left:179px;top:30px}
.consulting .body-text{position:absolute;left:179px;top:52px;width:258px}
.consulting .btn{position:absolute;left:179px;top:109px}
.team{height:142px;background:var(--lavender)}
.team .center-title{top:30px}
.member{position:absolute;top:54px;width:123px;height:56px;background:var(--white);display:flex;gap:4px;padding:3px}
.member-photo{width:49px;height:50px;flex:none}
.member-name{font-size:6.5px;color:#222;margin-top:2px}
.member-role{font-family:"Open Sans",sans-serif;font-size:4.5px;color:#333}
.member-bio{font-family:"Open Sans",sans-serif;font-size:3.4px;line-height:5px;color:#888;margin-top:3px}
.member-more{font-family:"Open Sans",sans-serif;font-size:3.6px;font-weight:600;color:#222}
.contact{height:190px}
.contact .center-title{top:31px}
.field{position:absolute;border:1px solid #c9c9c9;font-family:"Open Sans",sans-serif;font-size:4.5px;color:#888;padding:4px 6px}
.contact .btn{position:absolute;left:231px;top:141px;width:37px;height:16px;padding:0;text-align:center;line-height:16px;font-size:7px}
.site-footer{height:40px;background:var(--footer);position:relative;font-family:"Open Sans",sans-serif;color:#ddd}
.footer-links{position:absolute;left:60px;top:11px;font-size:4.5px;word-spacing:1px}
.footer-copy{position:absolute;left:60px;top:24px;font-size:4.5px;color:#bbb}
.site-footer .social{position:absolute;left:417px;top:17px}
.site-footer .social span{background:#ddd}
</style>
</head>
<body>

<!-- Landing screen -->
<div class="landing">
  <div class="landing-hero" role="img" aria-label="Purple digital background of glowing hexagon network lines, padlocks and binary code">
    <div class="landing-brand"><span class="brand-square"></span>LUMERA FIELDWORKS</div>

    <div class="hex-option" style="left:98px;top:79px">
      <svg viewBox="0 0 108 94" width="108" height="94">
        <polygon points="27,1 81,1 107,47 81,93 27,93 1,47" fill="#f2f2f2"/>
        <g fill="none" stroke="#6b449b" stroke-width="1.2">
          <rect x="46" y="22" width="16" height="11" rx="1"/>
          <path d="M49 22v-4a5 5 0 0 1 10 0v4"/>
          <line x1="40" y1="27" x2="46" y2="27"/><line x1="62" y1="27" x2="68" y2="27"/>
          <line x1="54" y1="33" x2="54" y2="38"/>
          <circle cx="38" cy="27" r="1.5"/><circle cx="70" cy="27" r="1.5"/><circle cx="54" cy="40" r="1.5"/>
        </g>
      </svg>
      <div class="hex-label">Cyber Security</div>
    </div>

    <div class="hex-option" style="left:292px;top:79px">
      <svg viewBox="0 0 108 94" width="108" height="94">
        <polygon points="27,1 81,1 107,47 81,93 27,93 1,47" fill="#f2f2f2"/>
        <g fill="none" stroke="#6b449b" stroke-width="1.2">
          <path d="M42 20h18a2 2 0 0 1 2 2v10a2 2 0 0 1-2 2h-12l-5 4v-4h-1a2 2 0 0 1-2-2v-10a2 2 0 0 1 2-2z"/>
          <path d="M62 24h4a2 2 0 0 1 2 2v8a2 2 0 0 1-2 2h-1v3l-4-3"/>
          <line x1="45" y1="25" x2="57" y2="25"/><line x1="45" y1="29" x2="54" y2="29"/>
        </g>
      </svg>
      <div class="hex-label">Cyber Security<br>Consulting</div>
    </div>
  </div>
  <footer class="landing-footer">
    <span>Copyright © 2018 Lumera Fieldworks. All rights reserved.</span>
    <span class="social"><span></span><span></span></span>
  </footer>
</div>

<!-- Home page -->
<div class="page">
  <header class="site-header">
    <div class="brand"><span class="brand-square"></span>LUMERA FIELDWORKS</div>
    <nav class="nav"><span class="active">Home</span><span>About</span><span>Products</span><span>Consulting</span><span>Executive Team</span><span>Contact</span></nav>
  </header>

  <div class="hero" role="img" aria-label="Hooded figure at a desk facing several glowing computer monitors, tinted purple">
    <svg class="hero-arrow" style="left:20px" viewBox="0 0 10 12"><path d="M7 1L2 6l5 5" fill="none" stroke="#fff" stroke-width="2"/></svg>
    <h1 class="hero-title">Etiam mattis augue<br>vehicula odio posuere</h1>
    <span class="btn-light">Contact Us</span>
    <svg class="hero-arrow" style="left:469px" viewBox="0 0 10 12"><path d="M3 1l5 5-5 5" fill="none" stroke="#fff" stroke-width="2"/></svg>
  </div>

  <section class="about">
    <h2 class="sec-title">About Lumera Fieldworks</h2>
    <p class="body-text">Lumera Fieldworks, LLC. Is a company that takes its roots from the idea of providing appropriate and creative solutions for cyber security operations, development and management. We have a mission first mindset for our clients and their objectives.</p>
    <span class="btn">Read More</span>
    <div class="ring" style="left:346px;top:34px"></div>
  </section>

  <section class="products">
    <h2 class="sec-title center-title">Products</h2>
    <svg class="slide-arrow" style="left:24px" viewBox="0 0 8 12"><path d="M6 1L2 6l4 5" fill="none" stroke="#666" stroke-width="1.2"/></svg>
    <div class="product-card" style="left:60px">
      <div class="product-img" role="img" aria-label="Dark blue circuit board with a glowing shield emblem" style="background:radial-gradient(circle at 50% 50%,#5b7390 0%,#243650 55%,#121c2c 100%)"></div>
      <div class="product-caption">Aliquam erat volutpat</div>
    </div>
    <div class="product-card" style="left:259px">
      <div class="product-img" role="img" aria-label="Isometric laptop with floating code screens on a cyan background" style="background:linear-gradient(135deg,#1a3c8a 0%,#1676c4 50%,#22d0e6 100%)"></div>
      <div class="product-caption">Vivamus eleifend vitae</div>
    </div>
    <svg class="slide-arrow" style="left:466px" viewBox="0 0 8 12"><path d="M2 1l4 5-4 5" fill="none" stroke="#666" stroke-width="1.2"/></svg>
  </section>

  <section class="consulting">
    <div class="ring" style="left:60px;top:34px"></div>
    <svg style="position:absolute;left:90px;top:64px" width="34" height="32" viewBox="0 0 34 32">
      <path d="M2 2h30v22h-8l6 7-12-7h-16z" fill="#4f2a8a"/>
      <g stroke="#fff" stroke-width="2"><line x1="8" y1="9" x2="26" y2="9"/><line x1="8" y1="13" x2="26" y2="13"/><line x1="8" y1="17" x2="26" y2="17"/></g>
    </svg>
    <h2 class="sec-title">Consulting</h2>
    <p class="body-text">Aliquam erat volutpat. Quisque aliquet ex nec est vestibulum pulvinar. Pellentesque convallis molestie enim sit amet efficitur. Etiam id imperdiet lectus. Vivamus lacus justo, ultrices nec erat in, euismod iaculis mauris. Vivamus eleifend vitae nulla.</p>
    <span class="btn">Read More</span>
  </section>

  <section class="team">
    <h2 class="sec-title center-title">Executive Team</h2>
    <div class="member" style="left:60px">
      <div class="member-photo" role="img" aria-label="Portrait photo of Martin Delacroix" style="background:linear-gradient(180deg,#cfcfcf,#6a6a6a)"></div>
      <div><div class="member-name">Martin Delacroix</div><div class="member-role">Founder &amp; CEO</div>
        <div class="member-bio">Martin has spent over a decade advising firms on security posture and risk.</div><div class="member-more">More</div></div>
    </div>
    <div class="member" style="left:188px">
      <div class="member-photo" role="img" aria-label="Portrait photo of Renata" style="background:linear-gradient(180deg,#d9c7a8,#9a7a5a)"></div>
      <div><div class="member-name">Renata</div><div class="member-role">Donec aliquam quam</div>
        <div class="member-bio">Fusce quis rhoncus nisi. Donec venenatis dignissim erat vitae varius.</div><div class="member-more">More</div></div>
    </div>
    <div class="member" style="left:316px">
      <div class="member-photo" role="img" aria-label="Portrait photo of Tobias" style="background:linear-gradient(180deg,#8a8a8a,#4a3a30)"></div>
      <div><div class="member-name">Tobias</div><div class="member-role">Aliquam dignissim</div>
        <div class="member-bio">Nullam sit amet viverra enim. Quisque pharetra erat et porta.</div></div>
    </div>
  </section>

  <section class="contact">
    <h2 class="sec-title center-title">Contact Us</h2>
    <div class="field" style="left:154px;top:54px;width:90px;height:17px">Name</div>
    <div class="field" style="left:254px;top:54px;width:90px;height:17px">Email</div>
    <div class="field" style="left:154px;top:80px;width:190px;height:50px">Message</div>
    <span class="btn">Submit</span>
  </section>

  <footer class="site-footer">
    <div class="footer-links">Home | About | Products | Consulting | Executive Team | Contact</div>
    <div class="footer-copy">Copyright © 2018 Lumera Fieldworks. All rights reserved.</div>
    <span class="social"><span></span><span></span></span>
  </footer>
</div>

</body>
</html>
```